Brellwick Partners, LLC Stationary

Brellwick Partners, LLC is a new financial planning and consulting company. We are looking for designs on business cards, letterhead, envelopes, and anything else that would be useful. Our preference for business card design is two sided. We are looking for a professional and clean look with incorporating the logo and patriotic feel. Thank you to all who participate and good luck!

```html
<!DOCTYPE html>
<html lang="en">
<head>
<meta charset="utf-8">
<title>Brellwick Partners, LLC — Business Card</title>
<link rel="stylesheet" href="https://fonts.googleapis.com/css2?family=Josefin+Sans:wght@300;400;600;700&display=swap">
<style>
  :root{
    --navy:#1d3f6b;
    --red:#c8222d;
    --white:#ffffff;
    --ink:#3a3a3a;
    --stage:#e9e6e1;
  }
  *{box-sizing:border-box;margin:0;padding:0}
  html,body{width:1200px;height:950px;overflow:hidden;background:var(--stage)}
  body{position:relative;font-family:"Josefin Sans",Arial,sans-serif}
  .card{position:absolute;width:600px;height:343px;overflow:hidden;box-shadow:0 8px 24px rgba(0,0,0,.18)}
  .card-bg{position:absolute;inset:0;width:100%;height:100%}

  /* Front */
  .card-front{left:80px;top:90px;background:var(--white)}
  .brand{position:absolute;left:44px;top:48px;color:var(--navy)}
  .brand-mark{display:inline-block;width:14px;height:14px;background:var(--navy);margin-right:10px;vertical-align:6px}
  .brand-name{font-weight:600;font-size:40px;letter-spacing:1px;line-height:1}
  .brand-sub{display:block;font-weight:600;font-size:16px;letter-spacing:2px;color:var(--navy);margin:6px 0 0 24px}
  .brand-tag{display:block;font-weight:400;font-size:9px;letter-spacing:1.6px;text-transform:uppercase;color:var(--navy);margin:5px 0 0 24px}

  .contact{position:absolute;right:40px;top:44px;list-style:none;color:var(--ink);font-weight:300;font-size:15px;line-height:1.55;text-align:right}
  .contact li{display:flex;justify-content:flex-end;align-items:center;gap:10px}
  .contact .addr{margin-bottom:10px}
  .icon{width:14px;height:14px;flex:none}

  .holder{position:absolute;left:40px;bottom:34px}
  .holder-name{font-weight:600;font-size:22px;letter-spacing:1.5px;color:var(--red);text-transform:uppercase}
  .holder-role{font-weight:300;font-size:18px;letter-spacing:1.5px;color:var(--white);text-transform:uppercase;margin-top:4px}

  /* Back */
  .card-back{left:520px;top:520px;background:var(--navy)}
  .back-brand{position:absolute;left:40px;bottom:40px;color:var(--white)}
  .back-name{display:block;font-weight:600;font-size:38px;letter-spacing:1px;line-height:1}
  .back-rule{display:block;height:1px;background:var(--white);width:240px;margin:8px 0 6px}
  .back-sub{display:block;font-weight:600;font-size:16px;letter-spacing:2px}
  .back-tag{display:block;font-size:9px;letter-spacing:1.6px;text-transform:uppercase;margin-top:4px}
  .back-web{display:block;font-size:14px;letter-spacing:4px;margin-top:10px;font-weight:300}
</style>
</head>
<body>

<section class="card card-front" aria-label="Business card front">
  <svg class="card-bg" viewBox="0 0 600 343" preserveAspectRatio="none" aria-hidden="true">
    <polygon points="0,230 600,300 600,343 0,343" fill="var(--navy)"/>
    <polygon points="0,206 600,282 600,290 0,214" fill="var(--red)"/>
    <polygon points="0,220 600,294 600,298 0,224" fill="var(--navy)"/>
  </svg>

  <div class="brand">
    <span class="brand-mark" aria-hidden="true"></span><span class="brand-name">BRELLWICK</span>
    <span class="brand-sub">PARTNERS, LLC</span>
    <span class="brand-tag">Financial planning and consulting</span>
  </div>

  <ul class="contact">
    <li>412 Alder Court</li>
    <li class="addr">Fairbanks, Alaska 99701</li>
    <li>555 210 4418
      <svg class="icon" viewBox="0 0 14 14" aria-hidden="true"><circle cx="7" cy="7" r="7" fill="var(--red)"/><path d="M4.5 3.5l1.5 0 .6 2-1 .8a5 5 0 0 0 2.1 2.1l.8-1 2 .6v1.5c-3.5.5-6.5-2.5-6-6z" fill="#fff"/></svg></li>
    <li>555 318 7702
      <svg class="icon" viewBox="0 0 14 14" aria-hidden="true"><circle cx="7" cy="7" r="7" fill="var(--red)"/><rect x="4" y="3" width="6" height="8" rx="1" fill="#fff"/></svg></li>
    <li>hello@brellwick.com
      <svg class="icon" viewBox="0 0 14 14" aria-hidden="true"><circle cx="7" cy="7" r="7" fill="var(--red)"/><rect x="3.5" y="4.5" width="7" height="5" fill="#fff"/><path d="M3.5 4.5l3.5 3 3.5-3" stroke="var(--red)" stroke-width=".8" fill="none"/></svg></li>
    <li>www.brellwick.com
      <svg class="icon" viewBox="0 0 14 14" aria-hidden="true"><circle cx="7" cy="7" r="7" fill="var(--red)"/><circle cx="7" cy="7" r="3.5" fill="none" stroke="#fff" stroke-width="1"/><path d="M3.5 7h7M7 3.5v7" stroke="#fff" stroke-width=".8"/></svg></li>
  </ul>

  <div class="holder">
    <p class="holder-name">Dana Whitfield</p>
    <p class="holder-role">CEO/Founder</p>
  </div>
</section>

<section class="card card-back" aria-label="Business card back">
  <svg class="card-bg" viewBox="0 0 600 343" preserveAspectRatio="none" aria-hidden="true">
    <polygon points="0,0 600,0 600,40 0,135" fill="var(--red)"/>
    <polygon points="0,135 600,40 600,80 0,172" fill="var(--white)"/>
  </svg>

  <div class="back-brand">
    <span class="back-name">BRELLWICK</span>
    <span class="back-rule" aria-hidden="true"></span>
    <span class="back-sub">PARTNERS, LLC</span>
    <span class="back-tag">Financial planning and consulting</span>
    <span class="back-web">www.brellwick.com</span>
  </div>
</section>

</body>
</html>
```